Fern Acupuncture Business Card Design

I would like a business card design for my acupuncture business which is based from 2 practices in Melbourne, Australia.

The front of the card should include:

*The Logo
* Name - Miranda Tesselhoff (B.App.Sc.(TCM), Dip.Rem.Mass.). (I would like the letters after my name in slightly smaller font)
* Mobile number - 0472 318 604
* Web address - www.fernacupuncture.com.au

On the back of the card I would somehow like to fit my 2 clinic addresses in. They are:

The Calm & Balance Rooms
842 Pellam St, Camberwell VIC 3124
Ph: 1300 287 419

Riverbend Natural Therapies & Herbal Practice
19 Quillon Ave, Malvern East VIC 3145
Ph: (03) 9731 4052

If there is space, I'd also like to add to the back of the card - Next Appointment............................ (or something along those lines).

Thanks and happy designing!

Target Market(s)

Health consumers, and colleagues in the health industry

Industry/Entity Type

Clinic

Contact Information for Business Card

as above in brief

Requirements
Must have
• I've seen some ok designs coming in, however I'd like to avoid the generic look with the added curved line details etc. I don't particularly need extra patterns added to the card. I'd prefer it to look quite clean and simple, and using more earthy colours (I'm not super keen on the lime green that a lot of designs seem to include. I don't mind the full black or white look, (obviously the back side needs to be a lighter colour to allow me to write appointment details on it). I also quite like the idea of the background looking like brown recycled paper (just an idea - that's not 100% necessary).
Nice to have
• I have an idea that I could have the main flower part of the logo printed as metallic.
Should not have
• Generic patterns and too much added detail.

```html
<!DOCTYPE html>
<html lang="en">
<head>
<meta charset="utf-8">
<title>Fern Acupuncture Business Card</title>
<link href="https://fonts.googleapis.com/css2?family=Open+Sans:wght@400;600;700&display=swap" rel="stylesheet">
<style>
  :root {
    --stage: #e9e6e1;
    --card: #161412;
    --card-top: #2a2622;
    --gold: #c9a04e;
    --bronze: #b08552;
    --sand: #d9c29a;
    --white: #f6f2ea;
    --muted: #b5aca0;
    --paper: #fbf8f2;
    --ink: #2a241e;
    --dots: #6b6155;
  }
  * { margin: 0; padding: 0; box-sizing: border-box; }
  html, body {
    width: 1200px; height: 913px; overflow: hidden;
    background: var(--stage);
    font-family: "Open Sans", Arial, sans-serif;
  }
  .card {
    position: absolute;
    width: 520px; height: 300px;
    border-radius: 4px;
    background: linear-gradient(160deg, var(--card-top) 0%, var(--card) 55%);
    box-shadow: 0 10px 28px rgba(0,0,0,.28);
    color: var(--white);
    overflow: hidden;
  }
  .card::after {
    content: ""; position: absolute; left: 0; right: 0; bottom: 0; height: 5px;
    background: linear-gradient(90deg, var(--bronze), var(--gold), var(--sand));
  }
  .card-front { left: 80px; top: 130px; }
  .card-back { left: 600px; top: 480px; }

  /* front */
  .brand {
    position: absolute; left: 30px; top: 82px;
    width: 190px; display: flex; flex-direction: column; align-items: center; gap: 14px;
  }
  .brand-mark {
    width: 84px; height: 84px; border-radius: 50%;
    background: radial-gradient(circle at 35% 30%, var(--sand), var(--gold) 55%, var(--bronze));
  }
  .brand-name {
    font-size: 17px; font-weight: 600; color: var(--white);
    letter-spacing: .5px; text-align: center;
  }
  .contact { position: absolute; left: 250px; top: 78px; }
  .contact-name { font-size: 20px; font-weight: 700; color: var(--gold); line-height: 1.2; }
  .contact-credentials { font-size: 11px; color: var(--muted); margin: 2px 0 16px; }
  .contact-row { display: flex; align-items: center; gap: 12px; font-size: 13px; margin-bottom: 9px; white-space: nowrap; }
  .contact-row svg { width: 13px; height: 13px; flex: none; }
  .icon-fill { fill: var(--sand); }
  .icon-line { fill: none; stroke: var(--sand); stroke-width: 2.2; }

  /* back */
  .clinics { position: absolute; left: 24px; top: 20px; right: 16px; }
  .clinics-title { font-size: 14px; font-weight: 700; color: var(--sand); letter-spacing: .4px; margin-bottom: 4px; }
  .clinic { display: flex; gap: 8px; font-size: 12px; line-height: 1.35; margin-bottom: 2px; }
  .clinic-bullet { color: var(--sand); font-weight: 700; }
  .clinic-name { color: var(--gold); font-weight: 700; font-size: 13px; }
  .clinic-address { color: var(--white); white-space: nowrap; }
  .appointment {
    position: absolute; left: 150px; right: 16px; top: 132px; bottom: 21px;
    background: var(--paper); color: var(--ink);
    padding: 26px 22px 0;
  }
  .appointment-line {
    display: flex; align-items: baseline; gap: 6px;
    font-size: 13px; height: 34px;
  }
  .appointment-line .fill { flex: 1; border-bottom: 2px dotted var(--dots); }
</style>
</head>
<body>

<section class="card card-front" aria-label="Business card front">
  <div class="brand">
    <div class="brand-mark"></div>
    <div class="brand-name">Fern Acupuncture</div>
  </div>
  <div class="contact">
    <div class="contact-name">Miranda Tesselhoff</div>
    <div class="contact-credentials">B.App.Sc.(TCM), Dip.Rem.Mass.</div>
    <div class="contact-row">
      <svg viewBox="0 0 24 24"><path class="icon-fill" d="M6.6 10.8a15.1 15.1 0 0 0 6.6 6.6l2.2-2.2a1 1 0 0 1 1-.25 11.4 11.4 0 0 0 3.6.57 1 1 0 0 1 1 1V20a1 1 0 0 1-1 1A17 17 0 0 1 3 4a1 1 0 0 1 1-1h3.5a1 1 0 0 1 1 1c0 1.25.2 2.45.57 3.57a1 1 0 0 1-.25 1z"/></svg>
      <span>0472 318 604</span>
    </div>
    <div class="contact-row">
      <svg viewBox="0 0 24 24"><path class="icon-line" d="M2 5h20v14H2z M2 5l10 8 10-8"/></svg>
      <span>miranda@fernacupuncture.com.au</span>
    </div>
    <div class="contact-row">
      <svg viewBox="0 0 24 24"><circle class="icon-line" cx="12" cy="12" r="10"/><path class="icon-line" d="M2 12h20M12 2c3 3 3 17 0 20M12 2c-3 3-3 17 0 20"/></svg>
      <span>www.fernacupuncture.com.au</span>
    </div>
  </div>
</section>

<section class="card card-back" aria-label="Business card back">
  <div class="clinics">
    <div class="clinics-title">CLINIC ADDRESSES</div>
    <div class="clinic">
      <span class="clinic-bullet">»</span>
      <div>
        <div class="clinic-name">The Calm &amp; Balance Rooms</div>
        <div class="clinic-address">842 Pellam St, Camberwell VIC 3124 &nbsp;•&nbsp; Ph: 1300 287 419</div>
      </div>
    </div>
    <div class="clinic">
      <span class="clinic-bullet">»</span>
      <div>
        <div class="clinic-name">Riverbend Natural Therapies &amp; Herbal Practice</div>
        <div class="clinic-address">19 Quillon Ave, Malvern East VIC 3145 &nbsp;•&nbsp; Ph: (03) 9731 4052</div>
      </div>
    </div>
  </div>
  <div class="appointment">
    <div class="appointment-line"><span>Next Appointment</span><span class="fill"></span></div>
    <div class="appointment-line"><span class="fill"></span></div>
    <div class="appointment-line"><span class="fill"></span></div>
  </div>
</section>

</body>
</html>
```